A poster for Natural Skincare which contains minerals and seaweed sourced from Australia

I need a poster designed for a skincare product range called Vorantelle. It contains natural ingredients sourced from Australia that pack a punch!

I'd like the tag line to say Advanced Skincare Formulas Given By Nature(or any other suggestion I'll consider)

As background the range includes a vitamin C serum, a skin radiance moisturiser made from seaweed and a Mask that contains a mineral with Zeolite
It's brightening, anti ageing, protective and nourishing, results are experienced very quickly.

I have uploaded photos of the packaging for look and feel and colour but let me know if you need to see more etc.

colour of font is attached

Industry/Entity Type

Health And Wellness

Requirements
Nice to have
• could I have some designs without faces and body parts also

```html
<!DOCTYPE html>
<html lang="en">
<head>
<meta charset="UTF-8">
<title>Vorantelle – Seaweed Extract, Vitamin C &amp; Zeolite</title>
<link rel="stylesheet" href="https://fonts.googleapis.com/css2?family=Cinzel:wght@400;500&family=Raleway:wght@300;500&display=swap">
<style>
  :root {
    --paper: #ffffff;
    --rose: #c4514f;
    --burgundy: #7c1f2e;
    --burgundy-deep: #65172a;
    --gold: #d6a247;
    --cream: #fbf3ee;
    --seaweed-light: #a8283a;
    --seaweed-dark: #6e1320;
  }
  html, body {
    margin: 0;
    padding: 0;
    overflow: hidden;
    background: var(--paper);
  }
  .poster {
    position: relative;
    width: 849px;
    height: 1200px;
    overflow: hidden;
    background: var(--paper);
  }
  .headline {
    position: absolute;
    top: 176px;
    left: 0;
    width: 100%;
    margin: 0;
    text-align: center;
    font-family: "Raleway", sans-serif;
    font-weight: 300;
    font-size: 41px;
    line-height: 48px;
    letter-spacing: 1px;
    color: var(--rose);
    text-transform: uppercase;
  }
  .product-visual {
    position: absolute;
    left: 0;
    top: 0;
    width: 849px;
    height: 1200px;
  }
  .brand-name {
    position: absolute;
    top: 722px;
    left: 330px;
    width: 300px;
    margin: 0;
    text-align: center;
    font-family: "Raleway", sans-serif;
    font-weight: 500;
    font-size: 44px;
    line-height: 52px;
    color: var(--cream);
  }
  .footer-band {
    position: absolute;
    left: 0;
    top: 0;
    width: 849px;
    height: 1200px;
  }
  .benefits {
    position: absolute;
    top: 1052px;
    left: 0;
    width: 100%;
    margin: 0;
    text-align: center;
    font-family: "Cinzel", serif;
    font-weight: 400;
    font-size: 35px;
    line-height: 46px;
    letter-spacing: 1px;
    color: var(--cream);
    text-transform: uppercase;
  }
  .divider {
    position: absolute;
    top: 1148px;
    left: 146px;
    width: 557px;
    height: 2px;
    background: var(--gold);
  }
  .tagline {
    position: absolute;
    top: 1156px;
    left: 0;
    width: 100%;
    margin: 0;
    text-align: center;
    font-family: "Cinzel", serif;
    font-weight: 500;
    font-size: 17px;
    line-height: 22px;
    letter-spacing: 0.5px;
    color: var(--gold);
    text-transform: uppercase;
  }
</style>
</head>
<body>
<main class="poster">
  <h1 class="headline">Seaweed Extract<br>Vitamin C &amp; Zeolite</h1>

  <svg class="product-visual" viewBox="0 0 849 1200" role="img" aria-label="Vorantelle skin radiance moisturiser box resting on a spread of red seaweed">
    <defs>
      <radialGradient id="seaweed-tone" cx="0.5" cy="0.55" r="0.6">
        <stop offset="0" stop-color="var(--seaweed-light)"/>
        <stop offset="1" stop-color="var(--seaweed-dark)"/>
      </radialGradient>
    </defs>
    <path fill="url(#seaweed-tone)" d="M120 700 C 110 640 170 600 230 610 C 250 560 300 520 360 540 C 390 470 470 410 520 440 C 560 400 610 420 620 470 C 680 470 720 520 700 570 C 760 580 820 620 790 680 C 830 720 810 790 750 790 C 740 850 680 880 620 860 C 590 920 520 940 470 900 C 420 930 350 910 330 870 C 270 890 200 860 200 810 C 130 810 90 760 120 700 Z"/>
  </svg>
  <p class="brand-name">Vorantelle</p>

  <svg class="footer-band" viewBox="0 0 849 1200" aria-hidden="true">
    <path d="M0 1005 Q 420 905 849 935 L 849 1200 L 0 1200 Z" fill="var(--burgundy)"/>
    <path d="M0 993 Q 420 893 849 922" fill="none" stroke="var(--gold)" stroke-width="3"/>
  </svg>

  <p class="benefits">Nourishing, Brightening,<br>Anti-Ageing, Protecting</p>
  <div class="divider"></div>
  <p class="tagline">Advanced Skincare Formulas Given by Nature</p>
</main>
</body>
</html>
```